Flyer Design Project

We are a start-up real estate brokerage looking to attract new agents. Our business relies heavily on technology to help give agents more time to spend with clients. Our model is also different from a typical broker in that we do not take a percentage of commission from each sale an agent makes. Instead we charge a simple flat monthly fee and the agent keeps 100% of the commission the earn.
The ideal flyer will be pleasing to the eye, should probably have some appropriate graphics, use our logo and project a modern yet sophisticated company image. This is and advertising flyer that will be followed up with a more detailed brochure (later project).
Updates

While I like the initial design I was looking for more of a change from my design.  Here are some clarifications:

The design should not included the "click" option so it can be used online or in print.  Instead include the site velmorkhomes.com/careers

I want more of a list of features with less description.  The list should have:
- Peak Ledger included
- No Commission Split
- No Floor Time... Leads sent directly to you
- E & O Insurance included
- All your listings showcased on Homvista.com
- Showing appointment solution.

Some description of each can be included but less of a question answer style than what I originally had.
It does not need to be a straight list, the items all need to be mentioned somewhere on the flyer but not necessarily in a list style.
Maybe an image of business meeting or greeting (agent joining).

Please do not hesitate to ask questions for clarification

The image of meeting or greeting is optional - you choose what you think is best.
Also, use of the "About Us" that was uploaded my be a good idea.  - I'm not sure on this either

Target Market(s)

current real estate agents and people considering a real estate career

Industry/Entity Type

Real Estate

Requirements
Must have
• Should list that we include "Peak Ledger" which is considered the top program for real estate agents (info and logos can be found at peakledger.com)
Should highlight our low cost structure ($350 per month) and no transaction fees.
Should highlight that no office time is required. We provide virtual office solutions to save time.
Our contact number (555) 482-7913 ext. 204
Nice to have
• Any other additional information from the attached flyers (which should not be used as a template as they all need to be designed in a later project).

```html
<!DOCTYPE html>
<html lang="en">
<head>
<meta charset="utf-8">
<title>Velmork Homes – Agent Recruitment Flyer</title>
<link href="https://fonts.googleapis.com/css2?family=Arimo:wght@400;700&family=Open+Sans:wght@400;600;700&display=swap" rel="stylesheet">
<style>
  :root {
    --page: #ffffff;
    --panel-top: #87888a;
    --panel-bottom: #ececec;
    --maroon: #7a2a2b;
    --maroon-dark: #5a1c1d;
    --ink: #222222;
    --body-ink: #2b2b2b;
    --muted: #3a3a3a;
    --white: #ffffff;
    --footer-dark: #151515;
    --footer-mid: #3c3c3c;
    --footer-light: #a9a9a9;
  }
  * { box-sizing: border-box; margin: 0; padding: 0; }
  html, body { width: 936px; height: 1200px; overflow: hidden; background: var(--page); }
  .flyer { position: relative; width: 936px; height: 1200px; background: var(--page); font-family: "Open Sans", Arial, sans-serif; }
  .hero-panel {
    position: absolute; left: 19px; top: 16px; width: 898px; height: 970px;
    background: linear-gradient(180deg, var(--panel-top) 0%, #9c9d9f 35%, #c9c9ca 70%, var(--panel-bottom) 100%);
  }
  .price-ribbon { position: absolute; left: 101px; top: 16px; width: 237px; height: 213px; }
  .price-ribbon__text {
    position: absolute; left: 101px; top: 16px; width: 237px; text-align: center;
    color: var(--white); font-family: "Arimo", Arial, sans-serif; font-weight: 700;
  }
  .price-ribbon__label { display: block; margin-top: 55px; font-size: 17px; letter-spacing: 0.2px; }
  .price-ribbon__amount { display: block; font-size: 66px; line-height: 58px; }
  .price-ribbon__period { display: block; font-size: 16px; margin-top: 6px; }
  .price-ribbon__note { display: block; font-size: 13px; font-weight: 400; margin-top: 6px; }
  .headline {
    position: absolute; left: 362px; top: 74px; width: 540px;
    font-family: "Arimo", Arial, sans-serif; font-weight: 700; font-size: 52px; line-height: 54px; color: var(--white);
  }
  .recruit-line {
    position: absolute; left: 19px; top: 280px; width: 898px; text-align: center;
    font-family: "Arimo", Arial, sans-serif; font-weight: 700; font-size: 35px; line-height: 41px; color: var(--white);
  }
  .features { position: absolute; left: 80px; top: 390px; width: 776px; list-style: none; text-align: center; color: var(--body-ink); }
  .feature { margin-bottom: 14px; font-size: 19px; line-height: 26px; }
  .feature__title { display: block; font-weight: 700; font-size: 20px; color: var(--ink); }
  .listing-note { position: absolute; left: 19px; top: 762px; width: 898px; text-align: center; font-size: 19px; font-weight: 600; color: var(--muted); }
  .contact-button {
    position: absolute; left: 227px; top: 809px; width: 483px; height: 102px;
    background: var(--maroon); border-radius: 7px; box-shadow: 5px 5px 0 #111;
    text-align: center; color: var(--white); font-family: "Arimo", Arial, sans-serif; font-weight: 700;
  }
  .contact-button__site { display: block; margin-top: 19px; font-size: 22px; }
  .contact-button__phone { display: block; font-size: 29px; margin-top: 2px; }
  .office-note { position: absolute; left: 19px; top: 926px; width: 898px; text-align: center; font-family: "Arimo", Arial, sans-serif; font-weight: 700; color: #111; }
  .office-note__title { font-size: 23px; display: block; }
  .office-note__sub { font-size: 16px; display: block; }
  .footer {
    position: absolute; left: 19px; top: 986px; width: 898px; height: 196px;
    background: linear-gradient(90deg, var(--footer-dark) 0%, var(--footer-dark) 30%, var(--footer-mid) 60%, var(--footer-light) 100%);
  }
  .brand-box {
    position: absolute; left: 103px; top: 1038px; width: 307px; height: 93px;
    border: 3px solid #8d8d8d; background: #1a1a1a;
    display: flex; align-items: center; justify-content: center; gap: 12px;
  }
  .brand-box__mark { width: 14px; height: 14px; background: var(--maroon); }
  .brand-box__name { font-family: "Open Sans", Arial, sans-serif; font-weight: 400; font-size: 30px; color: var(--white); letter-spacing: 1px; }
  .crm { position: absolute; left: 473px; top: 1034px; width: 250px; color: var(--white); font-family: "Arimo", Arial, sans-serif; }
  .crm__title { font-size: 20px; font-weight: 700; }
  .crm__stat { font-size: 14px; line-height: 16px; margin-top: 2px; }
  .crm__blurb { font-size: 9px; line-height: 11px; margin-top: 10px; width: 245px; }
  .device-art {
    position: absolute; left: 735px; top: 1000px; width: 182px; height: 170px; border-radius: 10px;
    background: linear-gradient(160deg, #2b2b2b 0%, #5e6d86 50%, #c9d1dc 100%);
  }
</style>
</head>
<body>
<main class="flyer">
  <div class="hero-panel"></div>

  <svg class="price-ribbon" viewBox="0 0 237 213" aria-hidden="true">
    <polygon points="0,0 237,0 237,213 118.5,170 0,213" fill="var(--maroon)"/>
    <rect x="0" y="0" width="10" height="209" fill="var(--maroon-dark)" opacity="0.5"/>
    <rect x="227" y="0" width="10" height="209" fill="var(--maroon-dark)" opacity="0.5"/>
  </svg>
  <div class="price-ribbon__text">
    <span class="price-ribbon__label">LOW COST STRUCTURE</span>
    <span class="price-ribbon__amount">$350</span>
    <span class="price-ribbon__period">per month</span>
    <span class="price-ribbon__note">no transaction fees</span>
  </div>

  <h1 class="headline">Keep 100% Of Your Commission</h1>

  <h2 class="recruit-line">We are currently seeking new and<br>experienced agents to join our growing firm</h2>

  <ul class="features">
    <li class="feature"><span class="feature__title">No Commission Split</span>
      Pay just $350 per month, no transaction fees, and keep 100% of your commission.</li>
    <li class="feature"><span class="feature__title">No Floor Time… Leads Sent Directly To You</span>
      Our lead system feeds prospects to you anytime, anywhere.</li>
    <li class="feature"><span class="feature__title">E &amp; O Insurance Included</span>
      No extra E&amp;O costs coming out of your pocket.</li>
    <li class="feature"><span class="feature__title">Peak Ledger Included</span>
      The top contact management program for real estate agents.</li>
    <li class="feature"><span class="feature__title">Showing Appointment Solution</span>
      Showings scheduled seven days a week, with the longest hours in the industry.</li>
  </ul>

  <p class="listing-note">All your listings showcased on Homvista.com</p>

  <div class="contact-button">
    <span class="contact-button__site">velmorkhomes.com/careers</span>
    <span class="contact-button__phone">(555) 482-7913 EXT. 204</span>
  </div>

  <p class="office-note">
    <span class="office-note__title">No Office Time is Required</span>
    <span class="office-note__sub">We Provide Virtual Office Solutions to Save Time</span>
  </p>

  <footer class="footer"></footer>
  <div class="brand-box">
    <span class="brand-box__mark"></span>
    <span class="brand-box__name">VELMORK HOMES</span>
  </div>
  <div class="crm">
    <p class="crm__title">Peak Ledger CRM™</p>
    <p class="crm__stat">74% of clients will give you a referral if you stay in touch.</p>
    <p class="crm__blurb">Build referrals and build your business with real estate’s most intuitive real estate customer contact management (CRM) software for agents and brokers.</p>
  </div>
  <div class="device-art" role="img" aria-label="Tablet and phones showing the CRM contact app"></div>
</main>
</body>
</html>
```